Business Card Makeover. Recreate a sleek modern design for our business card.

DO NOT COPY OUR CURRENT DESIGN. MUST BE ONE SIDED BUSINESS CARD.
Create a new business card design, using our new logo. Attached is a sample of our current design and new logo. Please note the address and email will change. The new address is 412 Corvell Harbor Point 40921 and our website will be www.delmarhollis.example.

We are an architectural and interior design firm. We prefer a clean modern look. Something that is refined and emulates excellence.

Industry/Entity Type

Architecture

Contact Information for Business Card

clean modern look, please do not copy our attached design.

Font styles to use
Other font styles liked:
• see attached business card font

Colors

Designer to choose colors to be used in the design.

Requirements
Must have
• Must have a modern appeal and resemble our current branding.
Nice to have
• modern font, our logo, legible name and titles progressive design
Should not have
• Do not add colors not reflected in our branding. Should not look like our current card.

```html
<!DOCTYPE html>
<html lang="en">
<head>
<meta charset="UTF-8">
<title>Delmar Hollis + Partners — Business Card</title>
<link href="https://fonts.googleapis.com/css2?family=Poppins:wght@300;400&display=swap" rel="stylesheet">
<style>
  :root {
    --backdrop: #d9d9d9;
    --card: #f6f6f6;
    --brand-blue: #1b7bc4;
    --ink: #4a4a4a;
    --ink-soft: #8c8c8c;
  }
  * { margin: 0; padding: 0; box-sizing: border-box; }
  html, body {
    width: 1200px; height: 923px; overflow: hidden;
    background: var(--backdrop);
    font-family: "Poppins", sans-serif;
  }
  .card {
    position: absolute; left: 50px; top: 147px;
    width: 1100px; height: 628px;
    background: var(--card);
    color: var(--ink);
  }
  .brand { position: absolute; left: 87px; top: 265px; }
  .brand-mark {
    position: absolute; left: 0; top: 0;
    width: 91px; height: 91px; border-radius: 50%;
    background: var(--brand-blue);
  }
  .brand-name {
    position: absolute; left: 104px; top: 2px;
    white-space: nowrap; font-size: 40px; font-weight: 400;
    letter-spacing: 2.5px; line-height: 1; color: var(--ink);
  }
  .brand-partners {
    position: absolute; left: 263px; top: 50px;
    white-space: nowrap; font-size: 12px; letter-spacing: 8px;
    color: var(--ink); line-height: 1;
  }
  .brand-tagline {
    position: absolute; left: 104px; top: 73px;
    white-space: nowrap; font-size: 20px; font-weight: 300;
    color: var(--ink); line-height: 1;
  }
  .divider {
    position: absolute; left: 555px; top: 187px;
    width: 1px; height: 253px; background: var(--brand-blue);
  }
  .person { position: absolute; left: 593px; top: 180px; }
  .person-name {
    font-size: 38px; font-weight: 400; color: var(--brand-blue);
    line-height: 1; white-space: nowrap;
  }
  .person-name .credentials { font-size: 24px; }
  .person-title {
    margin-top: 4px; font-size: 26px; font-weight: 300;
    color: var(--ink-soft); line-height: 1; white-space: nowrap;
  }
  .contacts {
    position: absolute; left: 597px; top: 274px; list-style: none;
  }
  .contacts li {
    display: flex; align-items: center; height: 31px;
    font-size: 28px; font-weight: 300; white-space: nowrap;
  }
  .contacts svg { width: 20px; height: 20px; margin-right: 13px; fill: var(--brand-blue); }
  .license {
    position: absolute; left: 593px; top: 415px;
    font-size: 28px; font-weight: 300; line-height: 1; white-space: nowrap;
  }
  .address {
    position: absolute; left: 0; right: 0; top: 557px;
    display: flex; justify-content: center; align-items: center;
    font-size: 27px; font-weight: 300; white-space: nowrap;
  }
  .address svg { width: 19px; height: 26px; margin-right: 11px; fill: var(--brand-blue); }
</style>
</head>
<body>
  <main class="card">
    <div class="brand">
      <span class="brand-mark"></span>
      <span class="brand-name">DELMAR HOLLIS</span>
      <span class="brand-partners">+ PARTNERS</span>
      <span class="brand-tagline">ARCHITECTURE + INTERIOR DESIGN</span>
    </div>

    <div class="divider"></div>

    <div class="person">
      <p class="person-name">MAREN TALBOT, <span class="credentials">AIA, LEED AP</span></p>
      <p class="person-title">Partner/ Project Architect</p>
    </div>

    <ul class="contacts">
      <li>
        <svg viewBox="0 0 24 24" aria-hidden="true"><path d="M6.6 10.8a15.2 15.2 0 0 0 6.6 6.6l2.2-2.2a1 1 0 0 1 1-.25 11.4 11.4 0 0 0 3.6.57 1 1 0 0 1 1 1V20a1 1 0 0 1-1 1A17 17 0 0 1 3 4a1 1 0 0 1 1-1h3.5a1 1 0 0 1 1 1c0 1.25.2 2.450.57 3.6a1 1 0 0 1-.25 1z"/></svg>
        404.555.0144
      </li>
      <li>
        <svg viewBox="0 0 24 24" aria-hidden="true"><path d="M6 2h12v6H6zM3 9h18a1 1 0 0 1 1 1v7h-4v5H6v-5H2v-7a1 1 0 0 1 1-1zm5 7v4h8v-4z"/></svg>
        404.555.0172
      </li>
      <li>
        <svg viewBox="0 0 24 24" aria-hidden="true"><path d="M2 5h20v14H2zm2 2v.5l8 5 8-5V7z"/></svg>
        maren@delmarhollis.example
      </li>
      <li>
        <svg viewBox="0 0 24 24" aria-hidden="true"><path d="M12 2a10 10 0 1 0 0 20 10 10 0 0 0 0-20zm-1 17.9A8 8 0 0 1 4.1 11L9 15.9V17a2 2 0 0 0 2 2zm6.9-2.5A2 2 0 0 0 16 16h-1v-3a1 1 0 0 0-1-1H8v-2h2a1 1 0 0 0 1-1V7h2a2 2 0 0 0 2-2v-.4a8 8 0 0 1 2.9 12.8z"/></svg>
        www.delmarhollis.example
      </li>
    </ul>

    <p class="license">LIC.# AA40917725</p>

    <p class="address">
      <svg viewBox="0 0 18 25" aria-hidden="true"><path d="M9 0a9 9 0 0 0-9 9c0 6.5 9 16 9 16s9-9.5 9-16a9 9 0 0 0-9-9zm0 13a4 4 0 1 1 0-8 4 4 0 0 1 0 8z"/></svg>
      412 Corvell Harbor Point 40921
    </p>
  </main>
</body>
</html>
```